Ridgeline Journeys business card

please see website
www.ridgelinejourneys.comau

info needed on card
Curtis Halvey
Ph
email
Adventure Riding GPS trails

please use my logo and colours off my site

Curtis Halvey
curtis@ridgelinejourneys.com

```html
<!DOCTYPE html>
<html lang="en">
<head>
<meta charset="utf-8">
<title>Ridgeline Journeys – Business Card</title>
<link rel="stylesheet" href="https://fonts.googleapis.com/css2?family=Open+Sans:wght@400;600;700;800&display=swap">
<style>
  :root {
    --bg: #e9e6e1;
    --charcoal: #2b2b2b;
    --charcoal-dark: #1f1f1f;
    --ink: #111111;
    --yellow: #ffc800;
    --paper: #ffffff;
    --rule: #bdbdbd;
    --muted: #e6e6e6;
  }
  * { box-sizing: border-box; margin: 0; padding: 0; }
  html, body {
    width: 1200px; height: 900px; overflow: hidden;
    background: var(--bg);
    font-family: "Open Sans", Arial, sans-serif;
  }
  .stage {
    width: 1200px; height: 900px;
    display: flex; flex-direction: column; align-items: center; justify-content: center;
    gap: 48px;
  }
  .card {
    position: relative;
    width: 640px; height: 366px;
    overflow: hidden;
    box-shadow: 0 6px 18px rgba(0,0,0,.18);
  }

  /* Shared brand lockup */
  .brand { display: flex; align-items: center; gap: 14px; }
  .brand__mark { width: 26px; height: 26px; background: var(--yellow); flex: none; }
  .brand__name {
    font-weight: 800; font-size: 34px; line-height: 1.02; letter-spacing: 1px;
    text-transform: uppercase;
  }
  .brand__line { display: block; white-space: nowrap; }

  /* Back side */
  .card--back {
    background: linear-gradient(180deg, var(--charcoal) 0%, var(--charcoal-dark) 100%);
    color: var(--paper);
  }
  .back-lockup {
    position: absolute; left: 0; right: 0; top: 92px;
    display: flex; flex-direction: column; align-items: center; gap: 16px;
  }
  .card--back .brand__name { color: var(--paper); }
  .tagline { font-size: 19px; font-weight: 400; color: var(--muted); line-height: 1.3; }
  .web-row {
    position: absolute; left: 28px; right: 28px; top: 262px;
    display: flex; align-items: center; gap: 18px;
  }
  .web-row__rule { flex: 1; height: 1px; background: var(--rule); }
  .web-row__url { font-size: 16px; color: var(--muted); }

  /* Front side */
  .card--front { background: var(--paper); color: var(--ink); }
  .card__shapes { position: absolute; inset: 0; }
  .holder {
    position: absolute; left: 80px; top: 26px;
    font-size: 18px; font-weight: 700;
  }
  .holder__last { color: var(--yellow); }
  .contact {
    position: absolute; left: 40px; top: 178px;
    list-style: none; display: flex; flex-direction: column; gap: 2px;
    font-size: 16px; line-height: 1.4;
  }
  .contact__item { display: flex; align-items: center; gap: 10px; white-space: nowrap; }
  .contact__icon { width: 12px; height: 12px; flex: none; }
  .card--front .brand { position: absolute; left: 350px; top: 138px; }
  .card--front .brand__name { color: var(--ink); font-size: 32px; }
</style>
</head>
<body>
<main class="stage">

  <section class="card card--back" aria-label="Business card back">
    <div class="back-lockup">
      <div class="brand">
        <span class="brand__mark"></span>
        <span class="brand__name"><span class="brand__line">Ridgeline</span><span class="brand__line">Journeys</span></span>
      </div>
      <p class="tagline">Adventure Riding GPS trails</p>
    </div>
    <div class="web-row">
      <span class="web-row__rule"></span>
      <span class="web-row__url">www.ridgelinejourneys.com</span>
      <span class="web-row__rule"></span>
    </div>
  </section>

  <section class="card card--front" aria-label="Business card front">
    <svg class="card__shapes" viewBox="0 0 640 366" width="640" height="366" aria-hidden="true">
      <polygon points="0,0 62,0 0,34" fill="var(--ink)"/>
      <polygon points="24,40 62,6 62,40" fill="var(--yellow)"/>
      <polygon points="0,262 238,318 226,334 0,288" fill="var(--ink)"/>
      <polygon points="258,316 640,316 640,366 236,366" fill="var(--yellow)"/>
    </svg>

    <p class="holder">Curtis <span class="holder__last">Halvey</span></p>

    <ul class="contact">
      <li class="contact__item">
        <svg class="contact__icon" viewBox="0 0 12 12" aria-hidden="true"><path d="M2 1h3l1 3-2 1a7 7 0 0 0 3 3l1-2 3 1v3c0 1-1 1-1 1A10 10 0 0 1 1 2s0-1 1-1z" fill="var(--yellow)"/></svg>
        <span>044-555 010 203</span>
      </li>
      <li class="contact__item">
        <svg class="contact__icon" viewBox="0 0 12 12" aria-hidden="true"><rect x="0.5" y="2" width="11" height="8" fill="var(--yellow)"/><path d="M1 2.5l5 4 5-4" stroke="var(--paper)" fill="none"/></svg>
        <span>curtis@ridgelinejourneys.com</span>
      </li>
      <li class="contact__item">
        <svg class="contact__icon" viewBox="0 0 12 12" aria-hidden="true"><path d="M5 7l2-2M4 5L2.5 6.5a2 2 0 0 0 3 3L7 8M8 7l1.5-1.5a2 2 0 0 0-3-3L5 4" stroke="var(--yellow)" stroke-width="1.4" fill="none"/></svg>
        <span>www.ridgelinejourneys.com.au</span>
      </li>
    </ul>

    <div class="brand">
      <span class="brand__mark"></span>
      <span class="brand__name"><span class="brand__line">Ridgeline</span><span class="brand__line">Journeys</span></span>
    </div>
  </section>

</main>
</body>
</html>
```